Coastline Premier Retreats Business Card Design

Design a business card for Coastline Premier Retreats. Look at the website for colors and reference. Card should have logo, name, title, office number, mobile number, email, URL and a tagline like, "Luxury Hotel & Resort Email Marketing" (This might change).

https://www.coastlinepremierretreats.example

The rest I will leave up to your imagination.

Contact Information for Business Card

Logo, name, title, office number, mobile number, email, URL and a tagline like, "Luxury Hotel & Resort Email Marketing" (This might change).

```html
<!DOCTYPE html>
<html lang="en">
<head>
<meta charset="utf-8">
<title>Coastline Premier Retreats – Business Card</title>
<link rel="stylesheet" href="https://fonts.googleapis.com/css2?family=Montserrat:wght@400;500;600;700&display=swap">
<style>
  :root {
    --orange: #f07522;
    --orange-light: #f6a978;
    --ink: #1f1d1e;
    --ink-soft: #4a4a4b;
    --paper: #f1f1f1;
    --paper-shade: #e4e4e4;
    --text-grey: #4d4d4d;
    --white: #ffffff;
    --backdrop: #d9d9d9;
  }
  html, body {
    margin: 0;
    width: 1200px;
    height: 1200px;
    overflow: hidden;
    background: var(--backdrop);
    font-family: "Montserrat", sans-serif;
  }
  .card {
    position: absolute;
    left: 180px;
    width: 840px;
    height: 480px;
    border-radius: 28px;
    overflow: hidden;
    box-shadow: 0 10px 24px rgba(0,0,0,0.18);
  }
  /* Front */
  .card-front {
    top: 90px;
    background: linear-gradient(90deg, var(--orange-light) 0%, var(--orange) 65%);
  }
  .front-name {
    position: absolute;
    left: 0; right: 0; top: 170px;
    text-align: center;
    color: var(--white);
    font-weight: 700;
    font-size: 46px;
    letter-spacing: 3px;
    text-transform: uppercase;
    line-height: 1.15;
  }
  .front-name span { display: block; font-size: 26px; letter-spacing: 10px; }
  .tagline-band {
    position: absolute;
    left: 0; right: 0; bottom: 0;
    height: 72px;
    background: linear-gradient(90deg, var(--ink-soft), #0b0b0b);
    color: var(--white);
    font-size: 22px;
    font-weight: 500;
    display: flex;
    align-items: center;
    justify-content: center;
  }
  /* Back */
  .card-back {
    top: 630px;
    background: linear-gradient(180deg, var(--paper) 0%, var(--paper-shade) 100%);
  }
  .contact-band {
    position: absolute;
    left: 0; right: 0; bottom: 0;
    height: 240px;
    background: linear-gradient(90deg, var(--ink-soft) 0%, var(--ink) 45%, var(--ink) 100%);
  }
  .back-logo {
    position: absolute;
    right: 50px; top: 48px;
    text-align: right;
    color: var(--ink);
    font-weight: 700;
    font-size: 26px;
    letter-spacing: 2px;
    text-transform: uppercase;
    line-height: 1.2;
  }
  .back-logo span { display: block; font-size: 15px; letter-spacing: 6px; }
  .person { position: absolute; left: 60px; top: 120px; }
  .person-name {
    margin: 0;
    color: var(--orange);
    font-weight: 700;
    font-size: 36px;
  }
  .person-title {
    margin: 4px 0 0;
    color: var(--text-grey);
    font-weight: 500;
    font-size: 21px;
  }
  .contact {
    position: absolute;
    left: 90px; top: 268px;
    margin: 0; padding: 0;
    list-style: none;
    color: var(--white);
    font-size: 19px;
    font-weight: 500;
  }
  .contact li { display: flex; align-items: center; gap: 12px; height: 30px; }
  .contact svg { width: 18px; height: 18px; flex: none; }
  .address {
    position: absolute;
    left: 120px; top: 396px;
    margin: 0;
    color: var(--white);
    font-size: 19px;
    font-weight: 500;
    font-style: normal;
    line-height: 1.35;
  }
</style>
</head>
<body>

<section class="card card-front">
  <div class="front-name">Coastline<span>Premier Retreats</span></div>
  <div class="tagline-band">Luxury Hotel &amp; Resort Email Marketing</div>
</section>

<section class="card card-back">
  <div class="contact-band"></div>

  <div class="back-logo">Coastline<span>Premier Retreats</span></div>

  <div class="person">
    <h1 class="person-name">Jordan Hale</h1>
    <p class="person-title">Founder &amp; Director</p>
  </div>

  <ul class="contact">
    <li>
      <svg viewBox="0 0 24 24" fill="var(--orange)" aria-hidden="true"><path d="M6.6 10.8a15.2 15.2 0 0 0 6.6 6.6l2.2-2.2a1 1 0 0 1 1-.25 11.4 11.4 0 0 0 3.6.57 1 1 0 0 1 1 1V20a1 1 0 0 1-1 1A17 17 0 0 1 3 4a1 1 0 0 1 1-1h3.5a1 1 0 0 1 1 1c0 1.25.2 2.45.57 3.57a1 1 0 0 1-.25 1z"/></svg>
      555.210.4800
    </li>
    <li>
      <svg viewBox="0 0 24 24" fill="none" stroke="var(--orange)" stroke-width="2.4" aria-hidden="true"><rect x="6" y="2" width="12" height="20" rx="2"/><line x1="11" y1="18" x2="13" y2="18"/></svg>
      555-309-7162
    </li>
    <li>
      <svg viewBox="0 0 24 24" fill="var(--orange)" aria-hidden="true"><path d="M2 5h20v14H2z"/><path d="M2 5l10 8 10-8" fill="none" stroke="#1f1d1e" stroke-width="1.8"/></svg>
      info@coastlinepremierretreats.example
    </li>
    <li>
      <svg viewBox="0 0 24 24" fill="none" stroke="var(--orange)" stroke-width="2.2" aria-hidden="true"><circle cx="12" cy="12" r="9"/><path d="M3 12h18M12 3c3 3 3 15 0 18M12 3c-3 3-3 15 0 18"/></svg>
      www.coastlinepremierretreats.example
    </li>
  </ul>

  <address class="address">4170 Harbor View Lane<br>Bayport Maine 04900</address>
</section>

</body>
</html>
```